Quorva - corporate Business Card

We need a good look and innovative business card for a new start up company based in Los Angeles called "Quorva". We are in a payment business, including payment card, app, and ewallet. We are expert in online payment and Card not present (CNP) transaction.
We need an innovative, modern business card.

Our logo font is Aero Matics

Target Market(s)

Startup - Bank - Online Payment - Card Manufacturing

Industry/Entity Type

Startup

Contact Information for Business Card

phone: 555 014 7396 - Address: 4172 Marlowe blvd, Tarvel Park, OR 97299

Requirements
Must have
• Message: innovative, professional, expert, high tech, trust, online payment expert, security
Nice to have
• no comment
Should not have
• no Comment

```html
<!DOCTYPE html>
<html lang="en">
<head>
<meta charset="utf-8">
<title>Quorva business card</title>
<link rel="stylesheet" href="https://fonts.googleapis.com/css2?family=Open+Sans:wght@400;600;700&display=swap">
<style>
  :root {
    --backdrop: #3a3532;
    --card: #ffffff;
    --brand-red: #c11d32;
    --ink-grey: #6f6f6f;
    --rule-grey: #9a9a9a;
    --blush: #f8ece8;
  }
  * { box-sizing: border-box; margin: 0; padding: 0; }
  html, body { width: 1200px; height: 780px; overflow: hidden; }
  body {
    background: var(--backdrop);
    font-family: "Open Sans", Arial, sans-serif;
    position: relative;
  }
  .card {
    position: absolute;
    top: 240px;
    width: 520px;
    height: 300px;
    background: var(--card);
    overflow: hidden;
    box-shadow: 0 14px 30px rgba(0,0,0,0.45);
  }
  .card--front { left: 60px; }
  .card--back { left: 620px; }

  .brand {
    position: absolute;
    display: flex;
    align-items: center;
    gap: 12px;
  }
  .brand__dot {
    width: 58px; height: 58px;
    border-radius: 50%;
    background: var(--brand-red);
  }
  .brand__name {
    color: var(--brand-red);
    font-weight: 600;
    font-size: 52px;
    line-height: 1;
    letter-spacing: 1px;
    text-transform: lowercase;
  }
  .card--front .brand { left: 50%; top: 50%; transform: translate(-50%, -50%); }
  .card--back .brand { right: 30px; top: 68px; }
  .card--back .brand__dot { width: 50px; height: 50px; }
  .card--back .brand__name { font-size: 44px; }

  .halo {
    position: absolute;
    left: 70px; top: -40px;
    width: 230px; height: 230px;
    border-radius: 50%;
    background: var(--blush);
  }

  .person { position: absolute; left: 30px; top: 146px; }
  .person__name {
    color: var(--brand-red);
    font-weight: 700;
    font-size: 17px;
    line-height: 1.2;
  }
  .person__role {
    color: var(--ink-grey);
    font-size: 13px;
    letter-spacing: 0.6px;
  }

  .rule {
    position: absolute;
    left: 28px; right: 40px;
    top: 190px;
    height: 1px;
    background: var(--rule-grey);
  }

  .contacts { position: absolute; left: 28px; top: 198px; list-style: none; }
  .contacts li {
    display: flex; align-items: center; gap: 6px;
    color: var(--ink-grey);
    font-size: 13px;
    line-height: 19px;
  }
  .contacts svg { width: 13px; height: 13px; flex: none; }

  .address {
    position: absolute;
    right: 40px; top: 222px;
    color: var(--ink-grey);
    font-size: 14px;
    line-height: 19px;
    font-style: normal;
    text-align: left;
  }
</style>
</head>
<body>
  <section class="card card--front" aria-label="Card front">
    <div class="brand">
      <span class="brand__dot"></span>
      <span class="brand__name">quorva</span>
    </div>
  </section>

  <section class="card card--back" aria-label="Card back">
    <div class="halo"></div>
    <div class="brand">
      <span class="brand__dot"></span>
      <span class="brand__name">quorva</span>
    </div>
    <div class="person">
      <p class="person__name">Dana Keller</p>
      <p class="person__role">Managing Director</p>
    </div>
    <div class="rule"></div>
    <ul class="contacts">
      <li>
        <svg viewBox="0 0 13 13" aria-hidden="true"><rect width="13" height="13" fill="#c11d32"/><path d="M3.5 3h2l.6 2-1.1.8a6 6 0 0 0 2.2 2.2L8 6.9l2 .6v2a1 1 0 0 1-1 1A6.5 6.5 0 0 1 2.5 4a1 1 0 0 1 1-1z" fill="#fff"/></svg>
        555 014 7396
      </li>
      <li>
        <svg viewBox="0 0 13 13" aria-hidden="true"><rect width="13" height="13" fill="#c11d32"/><rect x="2.5" y="3.5" width="8" height="6" fill="none" stroke="#fff" stroke-width="1"/><path d="M2.5 3.5l4 3.2 4-3.2" fill="none" stroke="#fff" stroke-width="1"/></svg>
        contact@quorvapay.com
      </li>
    </ul>
    <address class="address">4172 Marlowe blvd,<br>Tarvel Park, OR 97299</address>
  </section>
</body>
</html>
```